Veltrane Group Business Card Design

The CEO is looking for a new trendy look for his business card.
You can stay with current branding or come up with something new/creative. It can be 3D, including Medical Office buildings. You can use our logo in a variety of colors. Please include name, title, company name, company website, email address, cell number

Target Market(s)

Real Estate Development and Construction

Industry/Entity Type

Health care real estate

Contact Information for Business Card

Rohesh Kamdar, CEO M-604.781.2249 E-roheshkamdar@veltrane.com Address:4180 Lindqvist Ave, Tampa, FL 33482 www.veltrane.com

Font styles to use
Other font styles liked:
• Be creative

Requirements
Must have
• Creative, trendy look
Nice to have
• Please go to our website to get a feel- www. veltrane.com
Should not have
• small fonts

```html
<!DOCTYPE html>
<html lang="en">
<head>
<meta charset="utf-8">
<title>Veltrane Group Business Card</title>
<link href="https://fonts.googleapis.com/css2?family=Montserrat:wght@400;700;800&display=swap" rel="stylesheet">
<style>
  :root {
    --backdrop: #2a2a2a;
    --card-black: #1b1b1b;
    --card-panel: #1d1d1d;
    --logo-gloss: #0c0c0c;
    --paper-white: #ffffff;
    --ink-black: #111111;
    --text-light: #f2f2f2;
    --text-muted: #d4d4d4;
  }
  * { box-sizing: border-box; margin: 0; padding: 0; }
  html, body {
    width: 1200px; height: 1015px; overflow: hidden;
    background: var(--backdrop);
    font-family: "Montserrat", sans-serif;
  }
  .canvas {
    position: relative; width: 1200px; height: 1015px;
    display: flex; flex-direction: column; align-items: center; justify-content: center; gap: 55px;
  }
  .card {
    width: 700px; height: 400px; position: relative; overflow: hidden;
    box-shadow: 0 14px 30px rgba(0,0,0,0.55);
  }
  .card-front {
    background: var(--card-black);
    display: flex; align-items: center; justify-content: center;
  }
  .front-wordmark {
    font-weight: 800; font-size: 78px; letter-spacing: -2px;
    color: var(--logo-gloss);
  }
  .card-back { display: flex; background: var(--card-panel); }
  .brand-panel {
    width: 285px; background: var(--paper-white);
    display: flex; align-items: center; justify-content: center;
  }
  .brand-name {
    font-weight: 800; font-size: 40px; line-height: 1.05; letter-spacing: -1px;
    color: var(--ink-black); text-align: center;
  }
  .contact-panel {
    flex: 1; padding: 70px 0 0 48px; color: var(--text-muted);
  }
  .person-name { font-weight: 700; font-size: 24px; color: var(--text-light); }
  .person-title { font-size: 15px; margin-top: 2px; }
  .address { font-size: 15px; line-height: 1.35; margin-top: 26px; }
  .contact-list { list-style: none; margin-top: 20px; }
  .contact-list li {
    display: flex; align-items: center; gap: 12px;
    font-size: 15px; line-height: 1.7;
  }
  .contact-list svg { width: 14px; height: 14px; flex: none; }
</style>
</head>
<body>
<main class="canvas">
  <section class="card card-front">
    <span class="front-wordmark">Veltrane Group</span>
  </section>

  <section class="card card-back">
    <div class="brand-panel">
      <span class="brand-name">Veltrane<br>Group</span>
    </div>
    <div class="contact-panel">
      <p class="person-name">Rohesh Kamdar</p>
      <p class="person-title">CEO</p>
      <p class="address">4180 Lindqvist Ave,<br>Tampa, FL 33482</p>
      <ul class="contact-list">
        <li>
          <svg viewBox="0 0 16 16" aria-hidden="true"><path fill="#d4d4d4" d="M3.6 1.5l2.2 2.6-1.2 1.7c.9 2 2.6 3.7 4.6 4.6l1.7-1.2 2.6 2.2-1.4 2.3C6.8 13.5 2.5 9.2 1.3 3z"/></svg>
          604.781.2249
        </li>
        <li>
          <svg viewBox="0 0 16 16" aria-hidden="true"><rect x="1" y="3" width="14" height="10" fill="#d4d4d4"/><path d="M1 3l7 6 7-6" fill="none" stroke="#1d1d1d" stroke-width="1.4"/></svg>
          roheshkamdar@veltrane.com
        </li>
        <li>
          <svg viewBox="0 0 16 16" aria-hidden="true"><circle cx="8" cy="8" r="7" fill="#d4d4d4"/><path d="M1 8h14M8 1c-3 3.5-3 10.5 0 14M8 1c3 3.5 3 10.5 0 14" fill="none" stroke="#1d1d1d" stroke-width="1.1"/></svg>
          www.veltrane.com
        </li>
      </ul>
    </div>
  </section>
</main>
</body>
</html>
```